Online homewares store needs a web design

We need a web design for a new high-end online homewares store. We are starting small with only 5 major categories.

Rugs
Bathe
Dine
Decorative
Sleep

This is just for design. No coding needed.

Please make high-end, sophisticated and minimal.

I have included some pictures to give you an idea of the products. I would like to showcase some of the pictures on the web page.

The website will be using an e-commerce function.

I have included the logo studio nine harbors.

I like this website
http://mapleandquarrylane.example/

or

borvanest.example.au

Simple but effective - not too busy

Project Deadline Extended
Reason: I would like to extend my deadline to give designers more time to do quality work - as requested!! Thanks.

Target Market(s)

Females in the age bracket of 25-45

Males who are very house proud 25-45

Industry/Entity Type

Store

Requirements
Must have
• Upmarket

```html
<!DOCTYPE html>
<html lang="en">
<head>
<meta charset="utf-8">
<title>studio nine harbors — Homewares</title>
<link href="https://fonts.googleapis.com/css2?family=Nunito+Sans:wght@300;400;600;700&family=Raleway:wght@300&display=swap" rel="stylesheet">
<style>
  :root{
    --black:#000;
    --ink:#fff;
    --muted:#d6d6d6;
    --pink:#f0226e;
    --panel:#1f1f1f;
    --panel-edge:#2b2b2b;
    --footer:#2a2a2a;
    --caption:rgba(40,40,40,.72);
  }
  *{box-sizing:border-box;margin:0;padding:0}
  html,body{width:893px;height:1200px;overflow:hidden;background:var(--black)}
  body{position:relative;font-family:"Nunito Sans",Arial,sans-serif;color:var(--ink)}
  a{color:inherit;text-decoration:none}

  .site-header{position:absolute;left:0;top:0;width:893px;height:136px;background:var(--black)}
  .utility-links{position:absolute;left:551px;top:29px;font-size:11px;color:var(--ink)}
  .utility-links span{margin:0 5px}
  .cart{position:absolute;left:741px;top:29px;font-size:11px;display:flex;align-items:center;gap:6px}
  .brand{position:absolute;left:61px;top:54px;font-family:"Raleway",sans-serif;font-weight:300;font-size:41px;letter-spacing:-1px;color:var(--ink)}
  .main-nav{position:absolute;top:78px;left:0;font-size:12px;font-weight:600}
  .main-nav a{position:absolute;top:0;height:27px;line-height:27px;white-space:nowrap}
  .main-nav .active{background:var(--pink);padding:0 12px;left:510px}

  .hero{position:absolute;left:0;top:136px;width:893px;height:413px;
    background:linear-gradient(100deg,#6e6258 0%,#b9aa96 30%,#e6ddcf 55%,#cfc6b2 75%,#6f7d55 100%)}
  .hero-copy{position:absolute;left:160px;top:172px}
  .hero-title{position:absolute;left:160px;top:175px;font-size:32px;font-weight:700;white-space:nowrap}
  .hero-sub{position:absolute;left:160px;top:221px;font-size:16px;font-weight:400;white-space:nowrap}
  .hero-text{position:absolute;left:160px;top:251px;width:330px;font-size:12px;line-height:18px}
  .hero-arrow{position:absolute;top:184px;width:45px;height:45px}

  .showcase{position:absolute;left:0;top:549px;width:893px;height:547px;
    background:radial-gradient(ellipse at 50% 20%,#2c2c2c 0%,var(--panel) 60%,#181818 100%)}
  .welcome-title{position:absolute;left:0;top:40px;width:893px;text-align:center;color:var(--pink);font-size:25px;font-weight:400}
  .welcome-text{position:absolute;left:68px;top:84px;width:757px;text-align:center;font-size:11px;line-height:19px;color:var(--muted);font-weight:300}

  .category{position:absolute;width:237px;height:137px;overflow:hidden}
  .category-photo{position:absolute;inset:0}
  .category-bar{position:absolute;left:0;bottom:0;width:100%;height:36px;background:var(--caption);
    display:flex;align-items:center;justify-content:space-between;padding:0 12px 0 13px;font-size:14px;letter-spacing:.3px}

  .site-footer{position:absolute;left:0;top:1096px;width:893px;height:104px;background:var(--footer)}
  .footer-links{position:absolute;left:62px;top:34px;font-size:11px}
  .footer-links span{margin:0 5px}
  .copyright{position:absolute;left:62px;top:61px;font-size:11px}
  .social{position:absolute;top:34px;left:654px;display:flex;gap:11px}
</style>
</head>
<body>

<header class="site-header">
  <nav class="utility-links"><a href="#">Register</a><span>|</span><a href="#">Login</a><span>|</span><a href="#">My Account</a></nav>
  <a class="cart" href="#">
    <svg width="14" height="12" viewBox="0 0 14 12" aria-hidden="true"><path d="M0 1h2.5l2 7h7l1.5-5H4" fill="none" stroke="#ccc" stroke-width="1.2"/><circle cx="5.5" cy="10.5" r="1" fill="#ccc"/><circle cx="10.5" cy="10.5" r="1" fill="#ccc"/></svg>
    Cart (0) items
  </a>
  <div class="brand">studio nine harbors</div>
  <nav class="main-nav">
    <a class="active" href="#">HOME</a>
    <a href="#" style="left:586px">ABOUT US</a>
    <a href="#" style="left:671px">PRODUCTS</a>
    <a href="#" style="left:760px">CONTACT US</a>
  </nav>
</header>

<section class="hero" role="img" aria-label="Bright modern open-plan kitchen with island, bar stools and a dining table by garden doors">
  <h1 class="hero-title">DUIS AUTEM VEL EUM</h1>
  <h2 class="hero-sub">ELEIFEND OPTION CON &nbsp;ANTEPOSUERIT</h2>
  <p class="hero-text">Duis autem vel eum iriure dolor in hendrerit in vulputate velit esse molestie consequat el eu feugiat nulla.</p>
  <svg class="hero-arrow" style="left:64px" viewBox="0 0 45 45" aria-label="Previous slide"><circle cx="22.5" cy="22.5" r="22.5" fill="rgba(60,60,60,.55)"/><path d="M26 14l-8 8.5 8 8.5" fill="none" stroke="#fff" stroke-width="1.2"/></svg>
  <svg class="hero-arrow" style="left:782px" viewBox="0 0 45 45" aria-label="Next slide"><circle cx="22.5" cy="22.5" r="22.5" fill="rgba(60,60,60,.55)"/><path d="M19 14l8 8.5-8 8.5" fill="none" stroke="#fff" stroke-width="1.2"/></svg>
</section>

<main class="showcase">
  <h2 class="welcome-title">Welcome to Our Website</h2>
  <p class="welcome-text">Typi non habent claritatem insitam; est usus legentis in iis qui facit eorum claritatem. Investigationes demonstraverunt lectores legere me lquod ii unt saepius. Clarit as est etiam processus dynamicus, qui sequitur mutationem consuetudium lectorum. Mirum est notare quam litteothic.</p>

  <a class="category" href="#" style="left:76px;top:165px">
    <div class="category-photo" role="img" aria-label="Child's bare feet on a colourful felt ball rug" style="background:linear-gradient(135deg,#d94a6a,#e9b04a 35%,#5aa7c9 65%,#7c4fa0)"></div>
    <div class="category-bar">RUGS <svg width="20" height="20" viewBox="0 0 20 20"><circle cx="10" cy="10" r="9" fill="none" stroke="#fff" stroke-width="1.2"/><path d="M8.5 6l4 4-4 4" fill="none" stroke="#fff" stroke-width="1.2"/></svg></div>
  </a>
  <a class="category" href="#" style="left:330px;top:165px">
    <div class="category-photo" role="img" aria-label="White marble bathroom with glass shower and vanity" style="background:linear-gradient(135deg,#cfd0d0,#eeeeee 50%,#9c9c9a)"></div>
    <div class="category-bar">BATHE <svg width="20" height="20" viewBox="0 0 20 20"><circle cx="10" cy="10" r="9" fill="none" stroke="#fff" stroke-width="1.2"/><path d="M8.5 6l4 4-4 4" fill="none" stroke="#fff" stroke-width="1.2"/></svg></div>
  </a>
  <a class="category" href="#" style="left:582px;top:165px">
    <div class="category-photo" role="img" aria-label="Kitchen with turquoise splashback and yellow cabinets" style="background:linear-gradient(180deg,#e8e4d6 0%,#1fb3d6 40%,#1fb3d6 55%,#e3c62a 75%,#8d7a3c)"></div>
    <div class="category-bar">DINE <svg width="20" height="20" viewBox="0 0 20 20"><circle cx="10" cy="10" r="9" fill="none" stroke="#fff" stroke-width="1.2"/><path d="M8.5 6l4 4-4 4" fill="none" stroke="#fff" stroke-width="1.2"/></svg></div>
  </a>
  <a class="category" href="#" style="left:76px;top:349px">
    <div class="category-photo" role="img" aria-label="Strings of colourful beads hanging from a white lamp" style="background:linear-gradient(135deg,#f2f0ee,#e7d9dc 60%,#d64a6a)"></div>
    <div class="category-bar">DECORATIVE <svg width="20" height="20" viewBox="0 0 20 20"><circle cx="10" cy="10" r="9" fill="none" stroke="#fff" stroke-width="1.2"/><path d="M8.5 6l4 4-4 4" fill="none" stroke="#fff" stroke-width="1.2"/></svg></div>
  </a>
  <a class="category" href="#" style="left:330px;top:349px">
    <div class="category-photo" role="img" aria-label="Bed with green patterned quilt and a pink side table lamp" style="background:linear-gradient(135deg,#9a8fb0,#3f9c7f 45%,#2e7a63 70%,#e9e6e2)"></div>
    <div class="category-bar">SLEEP <svg width="20" height="20" viewBox="0 0 20 20"><circle cx="10" cy="10" r="9" fill="none" stroke="#fff" stroke-width="1.2"/><path d="M8.5 6l4 4-4 4" fill="none" stroke="#fff" stroke-width="1.2"/></svg></div>
  </a>
  <a class="category" href="#" style="left:582px;top:349px">
    <div class="category-photo" role="img" aria-label="Stack of colourful patchwork floor cushions" style="background:linear-gradient(90deg,#c46a3e,#4a9bb0 35%,#d9a24a 55%,#f4f4f4 80%)"></div>
    <div class="category-bar">CUSHION <svg width="20" height="20" viewBox="0 0 20 20"><circle cx="10" cy="10" r="9" fill="none" stroke="#fff" stroke-width="1.2"/><path d="M8.5 6l4 4-4 4" fill="none" stroke="#fff" stroke-width="1.2"/></svg></div>
  </a>
</main>

<footer class="site-footer">
  <nav class="footer-links"><a href="#">Home</a><span>|</span><a href="#">About Us</a><span>|</span><a href="#">Products</a><span>|</span><a href="#">Contact Us</a></nav>
  <p class="copyright">Copyright © 2013. All Rights Reserved.</p>
  <div class="social" aria-label="Social links">
    <svg width="35" height="35" viewBox="0 0 35 35"><circle cx="17.5" cy="17.5" r="16.5" fill="none" stroke="#ccc" stroke-width="1.5"/></svg>
    <svg width="35" height="35" viewBox="0 0 35 35"><circle cx="17.5" cy="17.5" r="16.5" fill="none" stroke="#ccc" stroke-width="1.5"/></svg>
    <svg width="35" height="35" viewBox="0 0 35 35"><circle cx="17.5" cy="17.5" r="16.5" fill="none" stroke="#ccc" stroke-width="1.5"/></svg>
    <svg width="35" height="35" viewBox="0 0 35 35"><circle cx="17.5" cy="17.5" r="16.5" fill="none" stroke="#ccc" stroke-width="1.5"/></svg>
  </div>
</footer>

</body>
</html>
```